corvale institute of business and technology web site

I need web site for the institute which focus on business courses and computer course it is also for vocation train for employment It is also carear development and advancement .It should have links to online study resource which free
Industry/Entity Type
Business
Number of Pages Required
1 page
Look and feel
Each slider illustrates characteristics of the customer's brand and the style your logo design should communicate.

```html
<!DOCTYPE html>
<html lang="en">
<head>
<meta charset="utf-8">
<title>Corvale Institute of Business and Technology</title>
<link rel="stylesheet" href="https://fonts.googleapis.com/css2?family=Open+Sans:wght@300;400;600;700&display=swap">
<style>
:root{
  --blue:#1e9be9;
  --blue-dark:#1683cc;
  --navy:#1f2552;
  --navy-deep:#171c42;
  --yellow:#f2b43a;
  --green:#2db35a;
  --ink:#2b2b2b;
  --muted:#6d6d6d;
  --strip:#e6e7ea;
  --white:#ffffff;
}
*{box-sizing:border-box;margin:0;padding:0}
html,body{width:1200px;height:2296px;overflow:hidden}
body{font-family:"Open Sans",Arial,sans-serif;color:var(--ink);background:var(--white);position:relative}
a{color:inherit;text-decoration:none}
ul{list-style:none}

/* hero */
.hero{position:absolute;left:0;top:0;width:1200px;height:428px;
  background:linear-gradient(120deg,#2a3f8f 0%,#3f6cc4 35%,#6f8fd6 60%,#3b4f9e 100%)}
.hero-shade{position:absolute;left:0;right:0;bottom:0;height:150px;background:linear-gradient(180deg,rgba(20,30,80,0),rgba(20,30,80,.55))}
.brand{position:absolute;left:40px;top:10px;display:flex;align-items:center;gap:10px;color:var(--white);font-weight:700;font-size:16px;letter-spacing:1px}
.brand-mark{width:70px;height:80px;background:var(--navy);border:3px solid var(--white)}
.top-nav{position:absolute;right:40px;top:58px;display:flex;gap:22px;color:var(--white);font-size:12px;font-weight:600;letter-spacing:.5px}
.top-social{position:absolute;right:40px;top:30px;display:flex;gap:8px}
.top-social span{width:14px;height:14px;border-radius:50%;background:rgba(255,255,255,.8)}
.hero-title{position:absolute;left:0;right:0;top:336px;text-align:center;color:var(--white);font-weight:300;font-size:32px;line-height:38px;letter-spacing:.5px;text-transform:uppercase}

/* program bar */
.program-bar{position:absolute;left:0;top:428px;width:1200px;height:44px;background:var(--blue);display:flex;justify-content:center;gap:44px;align-items:center;color:var(--white);font-size:12px;font-weight:700}

/* popular courses */
.popular{position:absolute;left:60px;top:520px;width:600px}
.popular h2{font-size:26px;line-height:32px;font-weight:700;text-transform:uppercase;color:var(--ink)}
.popular h2::before{content:"";display:block;width:60px;height:4px;background:var(--blue);margin-bottom:14px}
.popular p{margin-top:18px;font-size:13px;line-height:20px;color:var(--muted);width:480px}
.popular h3{margin-top:44px;font-size:14px;font-weight:700;color:var(--blue);text-transform:uppercase}
.program-list{margin-top:14px;display:grid;grid-template-columns:240px 280px;row-gap:8px;font-size:13px;color:var(--ink)}
.program-list li::before{content:"\203A";color:var(--blue);font-weight:700;margin-right:8px}

.course-tiles{position:absolute;left:712px;top:520px;width:432px;height:410px;display:grid;grid-template-columns:1fr 1fr;grid-template-rows:1fr 1fr;gap:4px}
.course-tile{background:var(--blue);color:var(--white);text-align:center;padding-top:46px}
.course-tile:nth-child(2),.course-tile:nth-child(3){background:var(--blue-dark)}
.course-tile svg{width:44px;height:44px}
.course-tile h4{margin-top:14px;font-size:14px;font-weight:700;text-transform:uppercase}
.course-tile p{margin:6px auto 0;font-size:12px;line-height:17px;width:160px}

/* strip & features */
.strip{position:absolute;left:0;top:960px;width:1200px;height:50px;background:var(--strip)}
.features{position:absolute;left:0;top:1010px;width:1200px;height:660px;background:var(--navy)}
.feature-grid{position:absolute;left:60px;top:30px;width:1080px;height:620px;display:grid;grid-template-columns:repeat(3,360px);grid-template-rows:330px 290px}
.feature{color:var(--white);text-align:center;padding:70px 36px 0}
.feature h4{font-size:17px;font-weight:600;text-transform:uppercase;letter-spacing:.5px}
.feature p{margin-top:18px;font-size:13px;line-height:20px}
.feature .more{display:inline-block;margin-top:22px;font-size:11px;font-weight:700;text-transform:uppercase}
.feature-blue{background:var(--blue)}
.feature-yellow{background:var(--yellow)}
.feature-green{background:var(--green);padding-top:50px}
.photo-grads{background:linear-gradient(160deg,#cfe0ee 0%,#9db7cf 45%,#2c2f3a 100%)}
.photo-library{background:linear-gradient(150deg,#8a6b4c 0%,#c9a77c 50%,#5b4635 100%)}
.photo-student{background:linear-gradient(160deg,#d7e6b6 0%,#a9c57d 45%,#6b8a4b 100%)}

/* partners */
.partners{position:absolute;left:0;top:1670px;width:1200px;height:240px;background:var(--white);display:flex;justify-content:center;align-items:center;gap:70px}
.partner-badge{width:150px;height:60px;background:#8a8d96;border-radius:4px}

/* footer */
.footer{position:absolute;left:0;top:1910px;width:1200px;height:340px;background:var(--navy-deep);color:#c9cbe0}
.footer-brand{position:absolute;left:60px;top:60px;width:200px;text-align:center}
.footer-brand .seal{width:90px;height:90px;border-radius:50%;background:#2d3566;border:3px solid #c9cbe0;margin:0 auto}
.footer-brand .name{margin-top:14px;font-size:13px;font-weight:700;color:var(--white);line-height:18px;text-transform:uppercase}
.footer-col{position:absolute;top:50px}
.footer-col h5{font-size:14px;font-weight:700;color:var(--white);text-transform:uppercase;margin-bottom:16px}
.footer-col li{font-size:11px;line-height:24px;text-transform:uppercase}
.social li{display:flex;align-items:center;gap:10px;text-transform:none;font-size:12px}
.social li span{width:16px;height:16px;border-radius:50%;background:var(--blue)}
.bottom-bar{position:absolute;left:0;top:2250px;width:1200px;height:46px;background:#12163a;color:#8f93b3;font-size:11px;padding:8px 60px;line-height:15px}
</style>
</head>
<body>

<header class="hero" role="img" aria-label="Photo of students studying together in a classroom, blue tint">
  <div class="hero-shade"></div>
</header>
<div class="brand"><span class="brand-mark"></span>CORVALE</div>
<div class="top-social"><span></span><span></span><span></span><span></span></div>
<nav class="top-nav"><a>HOME</a><a>ABOUT US</a><a>COURSES</a><a>APPLY ONLINE</a><a>SELF HELP</a></nav>
<h1 class="hero-title">Teamwork enhances productivity, performance<br>and skill development</h1>

<nav class="program-bar">
  <a>UNDER GRADUATE PROGRAMS</a><a>MASTER DEGREE PROGRAMS</a><a>POST GRADUATE PROGRAMS</a><a>IT COURSES</a><a>DIPLOMA COURSES</a>
</nav>

<section class="popular">
  <h2>Our popular IT<br>and business courses</h2>
  <p>Explore practical programs that build job ready skills in business, computing and management, with flexible study options and support from experienced faculty.</p>
  <h3>Popular programs &amp; courses</h3>
  <ul class="program-list">
    <li>Under Graduate Programs</li><li>Diploma Programs</li>
    <li>Master Degree Programs</li><li>Advanced Diploma Programs</li>
    <li>Post Graduate Programs</li><li>Finance &amp; Accounting Courses</li>
    <li>Certificate Level Programs</li><li>Website Information Technology (IT)</li>
  </ul>
</section>

<section class="course-tiles">
  <div class="course-tile">
    <svg viewBox="0 0 44 44" fill="none" stroke="#fff" stroke-width="2.5"><rect x="5" y="14" width="34" height="22" rx="2"/><path d="M16 14v-5h12v5M5 23h34"/></svg>
    <h4>Business courses</h4><p>Courses designed to boost your career and development</p>
  </div>
  <div class="course-tile">
    <svg viewBox="0 0 44 44" fill="none" stroke="#fff" stroke-width="2.5"><rect x="5" y="8" width="34" height="22" rx="2"/><path d="M16 38h12M22 30v8"/></svg>
    <h4>IT courses</h4><p>Courses designed to boost your career and development</p>
  </div>
  <div class="course-tile">
    <svg viewBox="0 0 44 44" fill="none" stroke="#fff" stroke-width="2.5"><circle cx="22" cy="22" r="16"/><circle cx="22" cy="22" r="9"/><circle cx="22" cy="22" r="2" fill="#fff"/></svg>
    <h4>Targeted audience</h4><p>Courses designed to boost your career and development</p>
  </div>
  <div class="course-tile">
    <svg viewBox="0 0 44 44" fill="none" stroke="#fff" stroke-width="2.5"><path d="M8 26v-4a14 14 0 0 1 28 0v4"/><rect x="6" y="24" width="7" height="11" rx="2"/><rect x="31" y="24" width="7" height="11" rx="2"/></svg>
    <h4>Technical support</h4><p>Courses designed to boost your career and development</p>
  </div>
</section>

<div class="strip"></div>

<section class="features">
  <div class="feature-grid">
    <div class="feature feature-blue">
      <h4>Excellent training</h4>
      <p>Learn from industry trainers through hands on sessions, guided projects and assessments that prepare you for real workplace challenges.</p>
      <a class="more">Click here to know more</a>
    </div>
    <div class="photo-grads" role="img" aria-label="Photo of graduates in caps and gowns"></div>
    <div class="feature feature-yellow">
      <h4>Motivate and achieve</h4>
      <p>Set clear career goals with mentors who guide your progress, celebrate milestones and help you reach new professional heights.</p>
      <a class="more">Click here to know more</a>
    </div>
    <div class="photo-library" role="img" aria-label="Photo of a student reading in a library"></div>
    <div class="feature feature-green">
      <h4>Digital technology</h4>
      <p>Access free online study resources, modern computer labs and digital tools that keep your learning flexible, current and practical.</p>
      <a class="more">Click here to know more</a>
    </div>
    <div class="photo-student" role="img" aria-label="Photo of a smiling student holding books outdoors"></div>
  </div>
</section>

<section class="partners">
  <div class="partner-badge"></div><div class="partner-badge"></div><div class="partner-badge"></div><div class="partner-badge"></div><div class="partner-badge"></div>
</section>

<footer class="footer">
  <div class="footer-brand"><div class="seal"></div><div class="name">Corvale Institute<br>of Business &amp; Technology</div></div>
  <div class="footer-col" style="left:370px"><h5>Quick links</h5>
    <ul><li>Home</li><li>About us</li><li>Courses</li><li>Apply online</li><li>Self help</li><li>Contact us</li></ul></div>
  <div class="footer-col" style="left:560px"><h5>Academics</h5>
    <ul><li>Course application forms</li><li>Exam dates</li><li>Application deadline</li><li>Study materials</li><li>Library</li><li>Free resources</li></ul></div>
  <div class="footer-col" style="left:780px"><h5>Campus</h5>
    <ul><li>Campus information</li><li>Digital etiquette</li><li>Terms &amp; conditions</li><li>Students view</li><li>Office help</li><li>Contacts</li></ul></div>
  <div class="footer-col" style="left:980px"><h5>Get connected</h5>
    <ul class="social"><li><span></span>Friendbook</li><li><span></span>Chirper</li><li><span></span>Circleplus</li><li><span></span>Viewtube</li></ul></div>
</footer>
<div class="bottom-bar">Copyright 2024 Corvale Institute. All rights reserved.<br>Terms &amp; Conditions | Privacy | Sitemap</div>

</body>
</html>
```